Business Card Design

Looking for business card designs for a new business. there will be two cards of the same design (both lots of information below in contact info). We would like the logo diagonally across the card with the information split above and below the logo similar to sketch. happy to look at similar alternatives
Please use same colours as in logo design

Industry/Entity Type

Business

Contact Information for Business Card

Dwight Halloran
mob - 0491 738 204
ph - 02 6148 3920
fax - 02 6148 3975
email - dwight@kestrelbeams.com.au
14 Larkmoor Road, Corrabin NSW 2361

Colin Marchetti
mob - 0438 912 557
ph - 02 6148 3920
fax - 02 6148 3975
email - colin@kestrelbeams.com.au

```html
<!DOCTYPE html>
<html lang="en">
<head>
<meta charset="utf-8">
<title>Kestrel Beams – Business Card</title>
<link rel="stylesheet" href="https://fonts.googleapis.com/css2?family=Open+Sans:wght@400;600;700&display=swap">
<style>
  :root {
    --teal: #1b7f7b;
    --ink: #111111;
    --paper: #ffffff;
    --text-grey: #333333;
    --backdrop: #e9e7e3;
    --divider: #8a8a8a;
  }
  * { margin: 0; padding: 0; box-sizing: border-box; }
  html, body {
    width: 1145px;
    height: 1200px;
    overflow: hidden;
    background: var(--backdrop);
    font-family: "Open Sans", Arial, sans-serif;
  }
  .canvas { position: relative; width: 1145px; height: 1200px; }

  .card {
    position: absolute;
    width: 943px;
    height: 539px;
    overflow: hidden;
    box-shadow: 0 3px 10px rgba(0,0,0,0.18);
  }
  .card--front { left: 21px; top: 34px; background: var(--paper); }
  .card--back  { left: 180px; top: 621px; background: var(--ink); }

  .brand {
    position: absolute;
    display: flex;
    align-items: center;
    gap: 18px;
    font-weight: 700;
    white-space: nowrap;
    letter-spacing: -0.5px;
  }
  .brand__mark { display: block; width: 68px; height: 68px; background: var(--teal); }
  .brand__name { font-size: 66px; line-height: 1; }
  .card--front .brand { left: 194px; top: 114px; width: 557px; height: 133px; justify-content: center; }
  .card--front .brand__name { color: var(--ink); }
  .card--back .brand { left: 0; top: 174px; width: 943px; height: 165px; justify-content: center; }
  .card--back .brand__mark { width: 84px; height: 84px; }
  .card--back .brand__name { color: var(--teal); font-size: 80px; }

  .person {
    position: absolute;
    right: 520px;
    top: 336px;
    text-align: right;
  }
  .person__name { color: var(--teal); font-weight: 700; font-size: 26px; line-height: 1; margin-bottom: 26px; }
  .person__address { color: var(--text-grey); font-size: 22px; line-height: 37px; }

  .divider {
    position: absolute;
    left: 441px;
    top: 329px;
    width: 1px;
    height: 144px;
    background: var(--divider);
  }

  .contacts {
    position: absolute;
    left: 454px;
    top: 329px;
    list-style: none;
  }
  .contacts li {
    display: flex;
    align-items: center;
    height: 36.5px;
    font-size: 23px;
    color: var(--ink);
  }
  .contacts li.contacts__email { font-size: 19px; }
  .contacts svg { width: 20px; height: 20px; margin-right: 8px; flex: none; fill: var(--teal); }

  .footer-band { position: absolute; left: 0; bottom: 0; width: 943px; height: 25px; display: block; }

  .website {
    position: absolute;
    left: 0;
    top: 428px;
    width: 943px;
    text-align: center;
    color: var(--paper);
    font-size: 29px;
    letter-spacing: 2px;
  }
  .website__domain { font-weight: 600; }
</style>
</head>
<body>
<main class="canvas">

  <section class="card card--front" aria-label="Card front">
    <div class="brand">
      <span class="brand__mark"></span>
      <span class="brand__name">Kestrel Beams</span>
    </div>

    <div class="person">
      <p class="person__name">Colin Marchetti</p>
      <p class="person__address">14 Larkmoor Road<br>Corrabin NSW 2361</p>
    </div>

    <div class="divider"></div>

    <ul class="contacts">
      <li>
        <svg viewBox="0 0 20 20" aria-hidden="true"><path d="M10 1a9 9 0 1 0 0 18 9 9 0 0 0 0-18zm0 1.8a7.2 7.2 0 1 1 0 14.4A7.2 7.2 0 0 1 10 2.8zM7.2 5.5l1.6 2.4-1 1.1c.7 1.4 1.8 2.5 3.2 3.2l1.1-1 2.4 1.6-.8 1.8c-3.8-.3-7.2-3.7-7.5-7.5z"/></svg>
        02 6148 3920
      </li>
      <li>
        <svg viewBox="0 0 20 20" aria-hidden="true"><path d="M6 1h8a1 1 0 0 1 1 1v16a1 1 0 0 1-1 1H6a1 1 0 0 1-1-1V2a1 1 0 0 1 1-1zm1 2v7h6V3zm0 9v1.6h1.6V12zm2.2 0v1.6h1.6V12zm2.2 0v1.6H13V12zM7 14.4V16h1.6v-1.6zm2.2 0V16h1.6v-1.6zm2.2 0V16H13v-1.6z"/></svg>
        0438 912 557
      </li>
      <li>
        <svg viewBox="0 0 20 20" aria-hidden="true"><path d="M5 3h10v4H5zM2 8h16a1 1 0 0 1 1 1v6h-3v-3H4v3H1V9a1 1 0 0 1 1-1zm3 5h10v5H5z"/></svg>
        02 6148 3975
      </li>
      <li class="contacts__email">
        <svg viewBox="0 0 20 20" aria-hidden="true"><path d="M2 8l8-6 8 6v10H2zm2 1.2V16h12V9.2l-6 4.3z"/></svg>
        colin@kestrelbeams.com.au
      </li>
    </ul>

    <svg class="footer-band" viewBox="0 0 943 25" preserveAspectRatio="none" aria-hidden="true">
      <polygon points="0,0 432,0 394,25 0,25" fill="var(--ink)"/>
      <polygon points="452,4 943,4 943,25 420,25" fill="var(--teal)"/>
    </svg>
  </section>

  <section class="card card--back" aria-label="Card back">
    <div class="brand">
      <span class="brand__mark"></span>
      <span class="brand__name">Kestrel Beams</span>
    </div>
    <p class="website">www.<span class="website__domain">kestrelbeams</span>.com.au</p>
  </section>

</main>
</body>
</html>
```